Simple and Clean business card design

We would like the design to be simple clean and to incorporate our colors.

We are open to your design and talent, we have the dots in our logo as we think of it as data points and we connect data points for people.

We are open to see the great creative and clean design you bring to the table

Contact Information for Business Card

please include: name, position, email, phone and website

Font styles to use
Sans Serif

Requirements
Must have
• my colors incorporated, simplicity
Nice to have
• lots of white space, simplicity
Should not have
• complexicity/ complex art

```html
<!DOCTYPE html>
<html lang="en">
<head>
<meta charset="utf-8">
<title>Meadowline Business Card</title>
<link href="https://fonts.googleapis.com/css2?family=Montserrat:wght@400;500;700&display=swap" rel="stylesheet">
<style>
  :root {
    --backdrop: #2a2b2d;
    --card: #1c1d1f;
    --white: #ffffff;
    --yellow: #f5b915;
    --blue: #5a7fc8;
    --muted: #d9d9d9;
  }
  * { margin: 0; padding: 0; box-sizing: border-box; }
  html, body {
    width: 1200px; height: 909px; overflow: hidden;
    background: var(--backdrop);
    font-family: "Montserrat", sans-serif;
  }
  .stage {
    width: 1200px; height: 909px;
    display: flex; align-items: center; justify-content: center;
  }
  .business-card {
    position: relative;
    width: 900px; height: 514px;
    background: var(--card);
    border-radius: 4px;
    box-shadow: 0 20px 50px rgba(0,0,0,.45);
    padding: 62px 70px;
    color: var(--white);
  }
  .brand {
    display: flex; align-items: center; gap: 14px;
  }
  .brand-dot {
    width: 30px; height: 30px; border-radius: 50%;
    background: var(--blue);
  }
  .brand-name {
    font-weight: 700; font-size: 58px; letter-spacing: -1px;
    color: var(--white); line-height: 1;
  }
  .person { margin-top: 44px; }
  .person-name {
    font-weight: 700; font-size: 30px; letter-spacing: 1px;
    text-transform: uppercase;
  }
  .person-name .first { color: var(--yellow); }
  .person-role {
    font-weight: 400; font-size: 24px; margin-top: 4px;
  }
  .contact-row {
    display: flex; align-items: flex-end; gap: 36px;
    margin-top: 40px;
  }
  .contact-list { list-style: none; }
  .contact-item {
    display: flex; align-items: center; gap: 14px;
    font-size: 20px; font-weight: 500; line-height: 1.6;
  }
  .contact-icon { width: 16px; height: 16px; flex: none; }
  .divider {
    width: 2px; height: 56px; background: var(--white);
    transform: skewX(-30deg); margin-bottom: 6px;
  }
  .address {
    font-style: normal; font-size: 20px; font-weight: 500; line-height: 1.4;
  }
</style>
</head>
<body>
<main class="stage">
  <section class="business-card">
    <header class="brand">
      <span class="brand-name">Meadowline</span>
      <span class="brand-dot"></span>
    </header>

    <div class="person">
      <h1 class="person-name"><span class="first">Marlo</span> Venner</h1>
      <p class="person-role">Founder/ CEO</p>
    </div>

    <div class="contact-row">
      <ul class="contact-list">
        <li class="contact-item">
          <svg class="contact-icon" viewBox="0 0 16 16" aria-hidden="true"><path fill="#f5b915" d="M3.5 1.5l2.5 3-1.5 1.5c.8 1.8 2.2 3.2 4 4l1.5-1.5 3 2.5-1.5 2.5C6.5 13.5 2.5 9.5 1 4z"/></svg>
          555-014-2290
        </li>
        <li class="contact-item">
          <svg class="contact-icon" viewBox="0 0 16 16" aria-hidden="true"><rect x="1" y="3" width="14" height="10" rx="1" fill="#f5b915"/><path d="M1.5 3.5L8 9l6.5-5.5" fill="none" stroke="#1c1d1f" stroke-width="1.4"/></svg>
          marlo.venner@meadowline.io
        </li>
        <li class="contact-item">
          <svg class="contact-icon" viewBox="0 0 16 16" aria-hidden="true"><circle cx="8" cy="8" r="7" fill="#f5b915"/><path d="M1 8h14M8 1c-3 3.5-3 10.5 0 14M8 1c3 3.5 3 10.5 0 14" fill="none" stroke="#1c1d1f" stroke-width="1.1"/></svg>
          www.meadowline.io
        </li>
      </ul>
      <span class="divider" aria-hidden="true"></span>
      <address class="address">18 Orchard Lane<br>Fairbrook, IL 60000</address>
    </div>
  </section>
</main>
</body>
</html>
```